Keystone Systems Line Card

I need to create a one page line card that displays the services that my company provides and the certifications we hold.
Updates
I have an updated logo that I will post as soon as I get it later today. For now you can see an example at:
The new logo is very close to this and the colors are the same.
The file that I have posted is an example of what I think is a slick format. the upload is a two page document, but I really only like the first page. What I need a little bit of marketing and then room for the content that describes our core services and certifications.
The content of the line card needs to be divided into 9 categories:
Cloud (Virtual) Computing environments
Links are to our current brochures on these items for reference.
Greetings all,
Greetings everyone!
Target Market(s)
Small to Medium sized businesses as well as government institutions. This should be a one page "firm handshake" type exposure that tells the customer they are dealing with a first class professional operation.
Industry/Entity Type
It Company
Look and feel
Each slider illustrates characteristics of the customer's brand and the style your logo design should communicate.

```html
<!DOCTYPE html>
<html lang="en">
<head>
<meta charset="utf-8">
<title>Keystone Systems Line Card</title>
<link href="https://fonts.googleapis.com/css2?family=Michroma&family=Open+Sans:wght@400;700&display=swap" rel="stylesheet">
<style>
  :root {
    --peach: #f0cfa3;
    --pale: #e6d4bc;
    --warm: #edcda2;
    --band: #dc9a45;
    --ink: #2a2620;
    --orange: #d77f12;
    --white: #ffffff;
  }
  html, body { margin: 0; padding: 0; overflow: hidden; }
  .card {
    position: relative;
    width: 845px; height: 1200px;
    background: var(--peach);
    overflow: hidden;
    font-family: "Open Sans", Arial, sans-serif;
    color: var(--ink);
  }
  .backdrop { position: absolute; inset: 0; }
  .brand-mark {
    position: absolute; left: 52px; top: 52px;
    width: 150px; height: 150px;
    background: var(--orange);
  }
  .brand-name {
    position: absolute; left: 248px; top: 66px;
    font-family: "Michroma", "Open Sans", sans-serif;
    font-size: 50px; line-height: 64px;
    color: var(--ink); margin: 0; font-weight: 400;
    letter-spacing: 1px;
  }
  .tagline {
    position: absolute; left: 360px; top: 188px;
    font-size: 18px; letter-spacing: 1.5px; margin: 0;
    color: var(--ink);
  }
  .service { position: absolute; left: 0; width: 845px; }
  .service-band {
    position: absolute; left: 0; width: 425px;
    background: var(--band);
  }
  .service-icon {
    position: absolute; left: 63px; width: 60px; height: 60px;
    background: var(--white); border: 3px solid var(--ink);
    border-radius: 10px;
  }
  .service-name {
    position: absolute; left: 157px; margin: 0;
    font-weight: 700; font-size: 29px; line-height: 1.15;
  }
  .service-name.small { font-size: 20px; }
  .service-text {
    position: absolute; left: 448px; width: 360px; margin: 0;
    font-size: 15.5px; line-height: 19.5px;
  }
  .footer {
    position: absolute; left: 0; top: 1112px;
    width: 640px; height: 40px; background: var(--ink);
  }
  .footer-url {
    position: absolute; left: 52px; top: 5px; margin: 0;
    color: var(--orange); font-weight: 700; font-size: 22px;
  }
</style>
</head>
<body>
<div class="card">
  <svg class="backdrop" width="845" height="1200" viewBox="0 0 845 1200">
    <polygon points="350,495 350,490 520,315 845,315 845,1200 400,1200" fill="var(--pale)"/>
    <rect x="595" y="555" width="250" height="535" fill="var(--warm)"/>
  </svg>

  <div class="brand-mark"></div>
  <h1 class="brand-name">KEYSTONE<br>SYSTEMS.NET</h1>
  <p class="tagline">ENTERPRISE SOLUTIONS FOR EVERYONE</p>

  <section class="service" style="top:250px">
    <div class="service-band" style="top:18px;height:39px"></div>
    <div class="service-icon" style="top:2px"></div>
    <h2 class="service-name" style="top:18px">BDR</h2>
    <p class="service-text" style="top:2px">Bulletproof your Data Protection with the Highest Industry Standards in an All-In-One Backup &amp; Business Continuity Solution</p>
  </section>

  <section class="service" style="top:340px">
    <div class="service-band" style="top:8px;height:55px"></div>
    <div class="service-icon" style="top:2px"></div>
    <h2 class="service-name small" style="top:10px">Cloud (Virtual)<br>Computing enviroments</h2>
    <p class="service-text" style="top:5px">Eliminate expensive start-up costs and IT management overhead with enterprise level cloud solutions.</p>
  </section>

  <section class="service" style="top:432px">
    <div class="service-band" style="top:18px;height:38px"></div>
    <div class="service-icon" style="top:2px"></div>
    <h2 class="service-name" style="top:17px">WorkSuite 365</h2>
    <p class="service-text" style="top:15px">The reliability of WorkSuite Office has now been enhanced with cloud features.</p>
  </section>

  <section class="service" style="top:520px">
    <div class="service-band" style="top:12px;height:38px"></div>
    <div class="service-icon" style="top:0"></div>
    <h2 class="service-name" style="top:11px">Outsourced IT</h2>
    <p class="service-text" style="top:13px">Keystone Systems provides customized Proactive IT monitoring and support that</p>
  </section>

  <section class="service" style="top:610px">
    <div class="service-band" style="top:12px;height:38px"></div>
    <div class="service-icon" style="top:0"></div>
    <h2 class="service-name" style="top:11px">Network Security</h2>
    <p class="service-text" style="top:5px">How secure is your network? Are you at risk? It´s time to get proactive!</p>
  </section>

  <section class="service" style="top:698px">
    <div class="service-band" style="top:13px;height:38px"></div>
    <div class="service-icon" style="top:2px"></div>
    <h2 class="service-name" style="top:12px">Server Care</h2>
    <p class="service-text" style="top:-2px">Flat-Rate Managed Server Care is a complete, 24x7x365 server monitoring, remediation, maintenance and management solution.</p>
  </section>

  <section class="service" style="top:790px">
    <div class="service-band" style="top:16px;height:39px"></div>
    <div class="service-icon" style="top:0"></div>
    <h2 class="service-name small" style="top:18px;font-size:23px">Desktop and user Care</h2>
    <p class="service-text" style="top:7px">Proactive Maintenance and Security Updates for your Workstations, Remote and On-Site IT Support for your Staff</p>
  </section>

  <section class="service" style="top:880px">
    <div class="service-band" style="top:13px;height:38px"></div>
    <div class="service-icon" style="top:0"></div>
    <h2 class="service-name" style="top:12px">VOIP</h2>
    <p class="service-text" style="top:-8px">Businesses that utilize VoIP save money and gain more communication features. Make a Smart Investment with your Small Business by switching to VoIP.</p>
  </section>

  <section class="service" style="top:968px">
    <div class="service-band" style="top:11px;height:39px"></div>
    <div class="service-icon" style="top:0"></div>
    <h2 class="service-name small" style="top:14px;font-size:24px">Vendor management</h2>
    <p class="service-text" style="top:1px">Get better, faster support for your third-party hardware and software investments and one point of contact for all of your vendor relationships.</p>
  </section>

  <footer class="footer">
    <p class="footer-url">www.keystonesystems.net</p>
  </footer>
</div>
</body>
</html>
```